Telecommunications/Power civil contractor needs business card design

Were a new telecommunications/power underground civil contractor that is looking for a new business card design. Our company colours are silver or grey and orange. Feel free to use the white background logo or the black background logo.

Target Market(s)

Local contractors, utility companies, private sector mining/energy companies, developers.

Industry/Entity Type

Telecommunications

Contact Information for Business Card

Each card will need the following info:
Persons name:
Title:
E-mail:
Phone number:
Shop Address:
Mailing Address:

Requirements
Must have
• Each card will need the following info:
• Persons name:
• Title:
• E-mail:
• Phone number:
• Shop Address:
• Mailing Address:

```html
<!DOCTYPE html>
<html lang="en">
<head>
<meta charset="utf-8">
<title>Delta Line Contracting Inc – Business Card</title>
<link href="https://fonts.googleapis.com/css2?family=Arimo:wght@400;700&display=swap" rel="stylesheet">
<style>
  :root {
    --page: #e9e7e4;
    --card: #1c1c1d;
    --orange: #e8581f;
    --silver: #a9abae;
    --text: #f2f2f2;
    --muted: #b9babc;
    --divider: #6d6e70;
  }
  * { margin: 0; padding: 0; box-sizing: border-box; }
  html, body {
    width: 1200px; height: 787px; overflow: hidden;
    background: var(--page);
    font-family: "Arimo", Arial, sans-serif;
  }
  .canvas {
    width: 1200px; height: 787px;
    display: flex; flex-direction: column;
    align-items: center; justify-content: center; gap: 34px;
  }
  .card {
    width: 600px; height: 350px;
    background: var(--card);
    position: relative;
    box-shadow: 0 6px 18px rgba(0,0,0,.18);
  }
  .brand {
    display: flex; flex-direction: column; align-items: center;
  }
  .brand-mark {
    width: 70px; height: 70px; border-radius: 50%;
    border: 5px solid var(--silver);
    margin-bottom: 12px;
  }
  .brand-name {
    color: var(--orange);
    font-weight: 700; text-transform: uppercase;
    letter-spacing: 1px; line-height: 1.1;
  }
  .brand-descriptor {
    color: var(--silver);
    font-weight: 700; text-transform: uppercase;
    letter-spacing: 2px; line-height: 1.2;
    margin-top: 4px;
  }
  .card-front { display: flex; align-items: center; justify-content: center; }
  .card-front .brand { margin-top: -30px; }
  .card-front .brand-name { font-size: 34px; }
  .card-front .brand-descriptor { font-size: 18px; }

  .card-back { display: flex; align-items: center; }
  .card-back .brand { width: 310px; }
  .card-back .brand-mark { width: 62px; height: 62px; border-width: 4px; }
  .card-back .brand-name { font-size: 28px; }
  .card-back .brand-descriptor { font-size: 14px; }
  .divider {
    width: 1px; height: 260px;
    background: linear-gradient(to bottom, transparent, var(--divider) 12%, var(--divider) 88%, transparent);
  }
  .contact { padding-left: 24px; color: var(--text); font-size: 14px; line-height: 1.3; }
  .contact-name { color: var(--orange); font-size: 19px; line-height: 1.2; }
  .contact-title { margin-bottom: 8px; }
  .contact-address { margin-bottom: 6px; }
  .address-label { color: var(--muted); font-size: 12px; text-transform: uppercase; letter-spacing: .5px; }
  .contact-list { list-style: none; margin-top: 8px; }
  .contact-list li { display: flex; align-items: center; gap: 10px; margin-bottom: 3px; }
  .icon { width: 13px; height: 13px; flex: none; }
</style>
</head>
<body>
<main class="canvas">
  <section class="card card-front">
    <div class="brand">
      <span class="brand-mark"></span>
      <p class="brand-name">Delta Line</p>
      <p class="brand-descriptor">Contracting Inc</p>
    </div>
  </section>

  <section class="card card-back">
    <div class="brand">
      <span class="brand-mark"></span>
      <p class="brand-name">Delta Line</p>
      <p class="brand-descriptor">Contracting Inc</p>
    </div>
    <div class="divider"></div>
    <div class="contact">
      <p class="contact-name">Mark Ellison</p>
      <p class="contact-title">President</p>
      <p class="contact-address"><span class="address-label">Shop</span><br>4120 Harbor Ridge Road<br>Oak Hollow, NY 11720</p>
      <p class="contact-address"><span class="address-label">Mailing</span><br>PO Box 318<br>Oak Hollow, NY 11720</p>
      <ul class="contact-list">
        <li>
          <svg class="icon" viewBox="0 0 16 16" aria-hidden="true"><path fill="#e8581f" d="M3.5 1 6 4 4.6 5.8a9 9 0 0 0 5.6 5.6L12 10l3 2.5-1.6 2.4C7.5 15 1 8.5 1.1 2.6Z"/></svg>
          <span>555 0142 7788</span>
        </li>
        <li>
          <svg class="icon" viewBox="0 0 16 16" aria-hidden="true"><rect x="1" y="3" width="14" height="10" fill="#e8581f"/><path d="M1 3l7 6 7-6" fill="none" stroke="#1c1c1d" stroke-width="1.4"/></svg>
          <span>mark@deltaline.com</span>
        </li>
        <li>
          <svg class="icon" viewBox="0 0 16 16" aria-hidden="true"><circle cx="8" cy="8" r="6.5" fill="none" stroke="#e8581f" stroke-width="1.6"/><path d="M1.5 8h13M8 1.5c-3 3.5-3 9.5 0 13M8 1.5c3 3.5 3 9.5 0 13" fill="none" stroke="#e8581f" stroke-width="1.2"/></svg>
          <span>www.deltaline.com</span>
        </li>
      </ul>
    </div>
  </section>
</main>
</body>
</html>
```